Web Design For Staffing Company

We need a homepage web design for a technical staffing company.

Please see attached brief for project details.

please make the site modern with bold colors while matching the logo

Be sure to read the attached breif in full beforehand.

Target Market(s)

technical companies looking to hire talent

Industry/Entity Type

Staffing

Number of Pages Required

1 page

Font styles to use
Sans Serif

```html
<!DOCTYPE html>
<html lang="en">
<head>
<meta charset="utf-8">
<title>Vantrix Staffing — Technical Staffing</title>
<link rel="stylesheet" href="https://fonts.googleapis.com/css2?family=Michroma&family=Oswald:wght@300;400;500&family=Montserrat:wght@400;600&display=swap">
<style>
:root{
  --navy:#13243f;
  --navy-2:#1b3a63;
  --blue:#2f73c4;
  --blue-bright:#3a86d6;
  --blue-btn:#2c6fc0;
  --grey:#ebebeb;
  --ink:#333;
  --white:#fff;
  --display:"Michroma",sans-serif;
  --cond:"Oswald",sans-serif;
  --sans:"Montserrat",sans-serif;
}
*{box-sizing:border-box;margin:0;padding:0}
html,body{width:1200px;height:3870px;overflow:hidden}
body{position:relative;background:var(--white);font-family:var(--cond);color:var(--ink)}
.abs{position:absolute}
.photo{position:absolute}
.btn{position:absolute;display:flex;align-items:center;justify-content:center;background:var(--blue-btn);color:#fff;font-family:var(--cond);font-weight:500;font-size:16px;text-transform:uppercase;letter-spacing:.3px;height:36px}
.btn.dark{background:#101c30}
.frame{position:absolute;border:1px solid #b9b9b9}
.frame.light{border-color:rgba(255,255,255,.55)}

/* header */
.site-header{left:0;top:0;width:1200px;height:145px;background:#fff}
.brand{left:80px;top:40px;display:flex;align-items:center;gap:10px;font-family:var(--display);font-size:30px;color:var(--navy-2)}
.brand .mark{width:34px;height:34px;background:var(--blue)}
.brand small{display:block;font-size:9px;letter-spacing:7px;margin-top:2px}
.nav{top:80px;left:515px;display:flex;gap:40px;font-family:var(--display);font-size:13px;color:var(--navy-2)}

/* search */
.search-band{left:0;top:145px;width:1200px;height:104px;background:linear-gradient(90deg,#1d3657 0%,#2a5e9c 45%,var(--blue-bright) 100%)}
.search-box{left:130px;top:175px;width:940px;height:56px;background:var(--blue-bright);padding:8px;display:flex;gap:8px}
.search-box span{background:#fff;flex:0 0 352px;font-size:14px;font-weight:300;padding:10px 14px;color:#444}
.search-box b{flex:1;background:var(--blue-btn);color:#fff;font-weight:500;display:flex;align-items:center;justify-content:center;font-size:16px}

/* hero */
.hero-slide{top:249px;width:600px;height:643px}
.hero-title{position:absolute;font-family:var(--display);color:#fff;font-size:31px;line-height:40px}
.arrow{position:absolute;width:46px;height:46px;border-radius:50%;display:flex;align-items:center;justify-content:center}

/* intro */
.intro{left:0;top:892px;width:1200px;height:171px;background:var(--grey);display:flex;align-items:center;justify-content:center;text-align:center;font-weight:300;font-size:19px;line-height:28px;color:#333}

/* sections */
.section-title{position:absolute;font-family:var(--display);font-size:32px}
.copy{position:absolute;font-weight:300;font-size:14px;line-height:28px}
.recruit{left:0;top:1063px;width:1200px;height:531px;background:linear-gradient(90deg,#142742 0%,#1f4a80 50%,var(--blue-bright) 100%)}
.testimonial{left:0;top:2088px;width:1200px;height:254px;background:linear-gradient(90deg,#1e4c86 0%,#163055 60%,#112440 100%);overflow:hidden}
.blog-card h3{position:absolute;font-family:var(--display);font-weight:400;font-size:24px;line-height:29px;color:#333}
.blog-card .date{position:absolute;font-weight:500;font-size:23px;color:var(--blue)}
.cta{top:3208px;width:600px;height:284px}
.cta h2{position:absolute;font-family:var(--display);font-weight:400;color:#fff;font-size:28px;line-height:35px}
.footer{left:0;top:3492px;width:1200px;height:316px;background:var(--navy)}
.footer h4{position:absolute;top:64px;color:#fff;font-weight:400;font-size:21px}
.footer p{position:absolute;top:125px;color:#fff;font-family:var(--sans);font-size:16px;line-height:28px}
.footer .fbtn{position:absolute;top:232px;width:315px;height:38px;background:var(--blue-btn);color:#fff;font-family:var(--sans);font-weight:600;letter-spacing:2px;font-size:15px;display:flex;align-items:center}
.fbtn i{width:46px;height:38px;background:#3b7dd0;display:flex;align-items:center;justify-content:center;margin-right:auto}
.fbtn em{font-style:normal;margin-right:28px}
.bottom-bar{left:0;top:3808px;width:1200px;height:62px;background:var(--blue);color:#fff;font-family:var(--sans);font-size:12px;display:flex;align-items:center;justify-content:center}
</style>
</head>
<body>

<header class="abs site-header">
  <div class="abs brand"><span class="mark"></span><div>Vantrix<small>STAFFING</small></div></div>
  <nav class="abs nav"><span>HOME</span><span>ABOUT</span><span>JOB SEEKERS</span><span>CLIENTS</span><span>CONTACT</span></nav>
</header>

<section class="abs search-band"></section>
<div class="abs search-box"><span>Keyword</span><span>Location</span><b>SEARCH JOBS</b></div>

<section class="abs hero-slide" style="left:0">
  <div class="photo" role="img" aria-label="Job candidates seated in a row holding job signs" style="inset:0;background:linear-gradient(135deg,#1c3f6b,#2a5f9e 60%,#2d6bb0)"></div>
  <h1 class="hero-title" style="left:86px;top:293px">THE RIGHT PEOPLE FOR<br>THE RIGHT JOBS!</h1>
  <span class="btn" style="left:88px;top:413px;width:170px;height:36px;font-family:var(--display);font-weight:400;font-size:14px">HIRE TALENT</span>
  <div class="arrow" style="left:540px;top:554px;background:#17304f"><svg width="14" height="14" viewBox="0 0 14 14"><path d="M9 2 4 7l5 5" stroke="#fff" stroke-width="2" fill="none"/></svg></div>
</section>
<section class="abs hero-slide" style="left:600px">
  <div class="photo" role="img" aria-label="Smiling technical professional holding a laptop with colleagues behind" style="inset:0;background:linear-gradient(135deg,#1f4f8c,#2f73c4 55%,#3a86d6)"></div>
  <h1 class="hero-title" style="left:54px;top:290px">BRIDGING THE TALENT<br>GAP IN TECHNICAL<br>STAFFING</h1>
  <span class="btn" style="left:56px;top:432px;width:174px">GET HIRED</span>
  <div class="arrow" style="left:11px;top:554px;background:#2a64ad"><svg width="14" height="14" viewBox="0 0 14 14"><path d="M5 2l5 5-5 5" stroke="#fff" stroke-width="2" fill="none"/></svg></div>
</section>

<section class="abs intro"><p>Vantrix Staffing is a National Technical Staffing and Recruiting Solutions Provider founded in 2013 focused on matching con-<br>tract and full time Engineering and IT professionals with new and exciting employment opportunities!</p></section>

<section class="abs recruit">
  <h2 class="section-title" style="left:208px;top:122px;color:#fff">Recruitment</h2>
  <p class="copy" style="left:208px;top:187px;width:380px;color:#fff">Simply said... WE LOVE TO RECRUIT! It's our passion and we take it very seriously! It is not easy for JOB SEEKERS to put their job search efforts and trust in the hands of someone else, especially when there are so many Staffing Firms to choose from. So how do you know you are choosing the best Staffing Representation possible?</p>
  <span class="btn" style="left:208px;top:380px;width:170px">LEARN MORE</span>
  <span class="btn" style="left:387px;top:380px;width:170px">VIEW JOBS</span>
  <div class="frame light" style="left:638px;top:120px;width:450px;height:272px"></div>
  <div class="photo" role="img" aria-label="Five candidates seated against a yellow wall" style="left:668px;top:155px;width:446px;height:274px;background:linear-gradient(135deg,#f5c21b,#f7cf3a)"></div>
</section>

<div class="frame" style="left:138px;top:1705px;width:450px;height:273px"></div>
<div class="photo" role="img" aria-label="Team meeting around a table with laptops" style="left:112px;top:1741px;width:446px;height:274px;background:linear-gradient(135deg,#c9c5c0,#e7e4e0 55%,#b9b4ad)"></div>
<h2 class="section-title" style="left:658px;top:1720px;color:var(--blue)">Technical Staffing</h2>
<p class="copy" style="left:658px;top:1780px;width:466px;color:#333">Are you responsible for Technical Staffing within your organization? Are you satisfied with your current Supplier(s)' overall performance? Does it appear they identify potential Candi-date(s) based purely on "buzz-word" searches? Is it evident they just do not grasp the scope and responsibilities of your technical staffing need(s)?</p>
<span class="btn" style="left:659px;top:1921px;width:170px">LEARN MORE</span>
<span class="btn" style="left:838px;top:1921px;width:170px">HIRE TALENT</span>

<section class="abs testimonial">
  <svg class="abs" style="left:0;top:0" width="400" height="254" role="img" aria-label="Person walking down a misty road">
    <defs><linearGradient id="tg" x1="0" x2="1"><stop offset="0" stop-color="#3e5068"/><stop offset="1" stop-color="#2a4a76"/></linearGradient></defs>
    <path d="M0 0H345L395 127 345 254H0Z" fill="url(#tg)"/>
  </svg>
  <h2 class="section-title" style="left:122px;top:108px;color:#fff;font-size:31px">Testimonial</h2>
  <div class="abs" style="left:435px;top:52px;color:#fff;font-weight:500;font-size:20px">– Sam R.</div>
  <div class="abs" style="left:435px;top:84px;color:#fff;font-weight:500;font-size:11px">Electrical Test Engineer in the Automotive Sector</div>
  <p class="copy" style="left:435px;top:114px;width:660px;color:#fff;font-size:13px">"Mark Delano is an excellent recruiter. He is articulate, honest, has a good nature and is an effective information conduit between his clients and candidates. He gave me the feeling he is there for the big picture desiring to forge a future relationship that will be mutually beneficial to both of us."</p>
</section>

<h2 class="section-title" style="left:0;width:1200px;text-align:center;top:2402px;color:var(--blue)">Vantrix Blog</h2>

<article class="blog-card">
  <div class="frame" style="left:100px;top:2485px;width:485px;height:290px"></div>
  <div class="photo" role="img" aria-label="Black and white portrait with a quote about technology" style="left:74px;top:2522px;width:479px;height:295px;background:linear-gradient(135deg,#1e1e1e,#4a4a4a 50%,#1a1a1a)"></div>
  <h3 style="left:88px;top:2848px">Tips for Spotting a U.S. Recession<br>Before It Becomes Official</h3>
  <div class="date" style="left:88px;top:2915px">June 19, 2019 by vantrixstaffing</div>
  <p class="copy" style="left:88px;top:2962px;width:500px;font-size:13px">As the U.S. nears a record-long expansion in July, the conversation is increasingly turning to when it will all end.</p>
  <span class="btn" style="left:91px;top:3035px;width:170px">READ MORE</span>
</article>
<article class="blog-card">
  <div class="frame" style="left:640px;top:2485px;width:485px;height:290px"></div>
  <div class="photo" role="img" aria-label="Woman smiling while working on a laptop" style="left:614px;top:2522px;width:479px;height:295px;background:linear-gradient(135deg,#d9d6cf,#8a7c6a 55%,#2e3c5a)"></div>
  <h3 style="left:623px;top:2848px">Ways To Make The Most Of The Hot<br>Job Market</h3>
  <div class="date" style="left:623px;top:2915px">June 17, 2019 by vantrixstaffing</div>
  <p class="copy" style="left:624px;top:2962px;width:500px;font-size:13px">"This is the tightest labor market I can remember. Unemployment is at a 50-year low and wage growth is at 3.2%," said Lena Brandt, chief economist for HireBoard.com, during the fifth-annual HireBoard Interactive conference, held last month in Austin, Texas.</p>
  <span class="btn" style="left:624px;top:3064px;width:170px">READ MORE</span>
</article>

<section class="abs cta" style="left:0">
  <div class="photo" role="img" aria-label="Professional working at a laptop in an office" style="inset:0;background:linear-gradient(135deg,#1f5fb0,#2f73c4 50%,#1c4e8e)"></div>
  <h2 style="left:98px;top:116px">Looking For Career - Minded<br>Candidates</h2>
  <span class="btn dark" style="left:101px;top:205px;width:170px">REQUEST TALENT</span>
</section>
<section class="abs cta" style="left:600px">
  <div class="photo" role="img" aria-label="Excited professional celebrating at a desk" style="inset:0;background:linear-gradient(135deg,#1a3e72,#245a9e 55%,#2a66b0)"></div>
  <h2 style="left:33px;top:118px">Looking For Career<br>Opportunities</h2>
  <span class="btn" style="left:35px;top:206px;width:170px">SEARCH JOB</span>
</section>

<footer class="abs footer">
  <h4 style="left:84px">GET HIRED</h4>
  <h4 style="left:440px">HIRE TALENT</h4>
  <h4 style="left:805px">ADDRESS</h4>
  <p style="left:84px;width:320px">Duis aute irure dolor in reprehenderit in voluptate velit esse cillum dolore</p>
  <p style="left:440px;width:320px">Duis aute irure dolor in reprehenderit in voluptate velit esse cillum dolore</p>
  <p style="left:805px;width:320px">Vantrix Staffing, Inc. 120 Harbor Street, Bldg. 2, 3rd floor Lakeview, MA 01920</p>
  <div class="fbtn" style="left:84px"><i><svg width="16" height="16" viewBox="0 0 16 16"><circle cx="7" cy="7" r="5" stroke="#fff" stroke-width="1.5" fill="none"/><path d="M11 11l4 4" stroke="#fff" stroke-width="1.5"/></svg></i><em>SEARCH NOW</em></div>
  <div class="fbtn" style="left:440px"><i><svg width="16" height="16" viewBox="0 0 16 16"><circle cx="8" cy="5" r="3.5" stroke="#fff" stroke-width="1.5" fill="none"/><path d="M2 15c0-4 12-4 12 0" stroke="#fff" stroke-width="1.5" fill="none"/></svg></i><em>START TODAY</em></div>
  <div class="fbtn" style="left:805px"><i><svg width="16" height="16" viewBox="0 0 16 16"><rect x="1.5" y="3.5" width="13" height="9" stroke="#fff" stroke-width="1.5" fill="none"/><path d="M2 4l6 5 6-5" stroke="#fff" stroke-width="1.5" fill="none"/></svg></i><em>CONTACT US</em></div>
</footer>
<div class="abs bottom-bar">© 2020 | www.vantrixstaffing.com</div>

</body>
</html>
```